Machining Business Order Thank You Insert

I am looking for a business style card to include with orders that I ship. The card needs to thank the recipient for their order, and encourage them to leave a review. The card should include my business name and contact information and have an area to hand write a message.

I mainly sale on Craftlane and my own website. We are a machining an manufacturing business that are in the sale of mostly metal machined and 3d printed plastic products.

The front of the card should include the following:
Logo: (attached)
Snapgram: https://www.snapgram.example/kelvomill/
Friendsbook: https://www.friendsbook.example/KelvoMill
Website: https://www.kelvomill.example/

The back of the card needs an area to write a message

Industry/Entity Type

3D Printing, Machining, Craftlane

Contact Information for Business Card

Black or white front, white back to write a personal message

Font styles to use
Sans Serif

Colors

Designer to choose colors to be used in the design.

Requirements
Must have
• Encourage a review, social media info

```html
<!DOCTYPE html>
<html lang="en">
<head>
<meta charset="utf-8">
<title>KelvoMill Order Thank You Card</title>
<link rel="stylesheet" href="https://fonts.googleapis.com/css2?family=Montserrat:wght@400;500;700&display=swap">
<style>
  :root {
    --page: #ffffff;
    --ink: #3a3a3a;
    --grey: #8c8c8c;
    --grey-band: #7d7d7d;
    --orange: #ee5a24;
    --card-dark-1: #1b1b1b;
    --card-dark-2: #0c0c0c;
    --card-light: #ffffff;
    --divider: #cfcfcf;
    --rule: #bdbdbd;
  }
  * { margin: 0; padding: 0; box-sizing: border-box; }
  html, body {
    width: 1200px;
    height: 2664px;
    overflow: hidden;
    background: var(--page);
    font-family: "Montserrat", sans-serif;
  }
  .canvas { position: relative; width: 1200px; height: 2664px; }

  .card {
    position: absolute;
    left: 120px;
    width: 960px;
    box-shadow: 0 6px 18px rgba(0,0,0,0.18);
    overflow: hidden;
  }

  /* Front side */
  .card-front {
    top: 1224px;
    height: 348px;
    background: linear-gradient(180deg, var(--card-dark-1), var(--card-dark-2));
    text-align: center;
  }
  .card-front .brand-name {
    position: absolute;
    left: 0; right: 0;
    top: 118px;
    font-size: 52px;
    font-weight: 500;
    letter-spacing: 14px;
    color: var(--grey);
    text-transform: uppercase;
  }
  .card-front .site {
    position: absolute;
    left: 0; right: 0;
    top: 256px;
    font-size: 20px;
    letter-spacing: 2px;
    color: #d8d8d8;
  }

  /* Back side */
  .card-back {
    top: 1712px;
    height: 700px;
    background: var(--card-light);
  }
  .card-back .brand-name {
    position: absolute;
    left: 48px;
    top: 296px;
    width: 430px;
    text-align: center;
    font-size: 48px;
    font-weight: 500;
    letter-spacing: 12px;
    color: var(--grey);
    text-transform: uppercase;
  }
  .card-back .divider {
    position: absolute;
    left: 500px;
    top: 72px;
    width: 2px;
    height: 520px;
    background: var(--divider);
  }
  .message {
    position: absolute;
    left: 532px;
    top: 64px;
    width: 400px;
  }
  .message .thanks {
    font-size: 46px;
    font-weight: 700;
    color: var(--ink);
    line-height: 1.1;
  }
  .message .review-prompt {
    margin-top: 8px;
    font-size: 22px;
    font-weight: 700;
    color: var(--orange);
  }
  .contact-list { list-style: none; margin-top: 30px; }
  .contact-list li {
    display: flex;
    align-items: center;
    gap: 18px;
    height: 50px;
    font-size: 20px;
    color: var(--ink);
  }
  .contact-list .dot {
    width: 30px; height: 30px;
    border-radius: 50%;
    background: var(--orange);
    flex: none;
  }
  .note-area { margin-top: 22px; }
  .note-area .note-label {
    font-size: 16px;
    font-weight: 500;
    color: var(--grey);
    letter-spacing: 1px;
    text-transform: uppercase;
  }
  .note-area .write-line {
    height: 40px;
    border-bottom: 2px solid var(--rule);
  }
  .footer-band { position: absolute; left: 0; bottom: 0; width: 960px; height: 60px; }
</style>
</head>
<body>
<main class="canvas">

  <section class="card card-front" aria-label="Card front">
    <div class="brand-name">KelvoMill</div>
    <div class="site">www.kelvomill.example</div>
  </section>

  <section class="card card-back" aria-label="Card back">
    <div class="brand-name">KelvoMill</div>
    <div class="divider"></div>
    <div class="message">
      <div class="thanks">Thank You!</div>
      <div class="review-prompt">Loved it? Please leave a review</div>
      <ul class="contact-list">
        <li><span class="dot"></span>www.kelvomill.example</li>
        <li><span class="dot"></span>snapgram.example/kelvomill</li>
        <li><span class="dot"></span>friendsbook.example/KelvoMill</li>
      </ul>
      <div class="note-area" aria-label="Space for a handwritten note">
        <div class="note-label">A note for you</div>
        <div class="write-line"></div>
        <div class="write-line"></div>
        <div class="write-line"></div>
      </div>
    </div>
    <svg class="footer-band" viewBox="0 0 960 60" aria-hidden="true">
      <path d="M0 14 H360 C390 14 400 34 430 34 H0 Z" fill="var(--grey-band)"/>
      <path d="M0 34 H430 L430 60 H0 Z" fill="var(--grey-band)"/>
      <rect x="440" y="40" width="520" height="10" fill="var(--orange)"/>
    </svg>
  </section>

</main>
</body>
</html>
```